Viral food truck (ClipCrowd) needs menu

Our food truck has gone viral on ClipCrowd and we're now requesting a one-page food menu for a taco food truck, please use the logo attached as inspiration and stick to those colors when designing the menu. This is a bilingual menu, please ensure to make the English translation stand out as well.

Size: 8x12 landscape

LOGO - Morales's Burrito Hut
812 W Orchard Ct (Entrada/Entrance Brightway Shopping Center)
Maple Hollow, NY 11845
Fri, 6 pm to 11:30 pm | Sat, 1 pm to 11:30 pm | Sun, 1 pm to 11:00 pm

Para horario y información / For pop-up, updated hours and information
Síganos/Follow Us: @moralesburritohut

MENU

Tacos.....$4.75 ea
Selección de carne, cilantro, cebolla, salsa roja o verde
Choice of meat, cilantro, onion, red or green salsa

Selección de carne/Choice of Meat
Pollo (Chicken)
Carne Asada (Steak)
Al pastor (Marinated Pork)
Chorizo (Sausage)
Carnitas (Pulled Pork)
Mixta (steak & sausage)........$0.75 extra
Suadero (Brisket).......$0.75 extra
Lengua (Beef Tongue)......$0.75 extra
Tripa (Beef Tripe)......$0.75 extra

Antojitos/Appetizers
Tacos Dorados De Pollo.......$15.00
Taco Dorados De Carne.........$15.00
Quesadilla...........$10.00
Pollo (Chicken) | Carne Asada (Steak) | Queso (Cheese)
Pupusa Revueltas (Chicharone y Queso).........$3.50
Pupusa Queso............$3.50

Especiales / Specials
(#1) 4 Tacos..........$14
(#2) 4 Tacos Dorados/Flautas
Pollo, Creama, Queso Fresco, Aguacate
Chicken, Cream, Queso Fresco, Avocado
*(designer note: need a symbol here) (#3) Chicharones 1lb........$25.00

* Cantidad limitada y temoprada/Limited Quantity/Seasonal

BEBIDAS/BEVERAGES

Horchata.........$6.00

Agua Fresca.......$5.00
SABOR/FLAVOR
Limonada (Lemonade) | Jamaica (Hibiscus) | Sandia (Watermelon) | Piña (Pineapple) | Melon | Mango

Fizzo......$2.00
Zestle.....$2.00
Water.....$1.50
Frutinas.......$3.00

Target Market(s)

Foodies

Industry/Entity Type

Food truck

Font styles to use
Sans Serif

Colors

Designer to choose colors to be used in the design.

Requirements
Must have
• Color and elements based on our logo, please also visit our SnapReel and FriendHub page for inspiration
Nice to have
• Vintage esthetic

```html
<!DOCTYPE html>
<html lang="en">
<head>
<meta charset="utf-8">
<title>Morales's Burrito Hut – Menu</title>
<link href="https://fonts.googleapis.com/css2?family=Oswald:wght@400;600&family=Roboto+Condensed:wght@400;700&display=swap" rel="stylesheet">
<style>
:root{
  --stage:#e7e4df;
  --paper:#f0e2c2;
  --paper-edge:#d9c191;
  --brown:#4a2616;
  --brown-soft:#7a5236;
  --red:#b3261e;
  --yellow:#f4c62a;
  --ink:#3a2214;
}
*{box-sizing:border-box;margin:0;padding:0}
html,body{width:889px;height:1200px;overflow:hidden}
body{background:var(--stage);font-family:'Roboto Condensed',sans-serif;color:var(--ink);position:relative}
.menu{position:absolute;left:10px;top:320px;width:869px;height:560px;
  background:radial-gradient(ellipse at center,var(--paper) 55%,var(--paper-edge) 100%);
  box-shadow:0 4px 14px rgba(0,0,0,.2);display:grid;grid-template-columns:270px 290px 1fr;gap:14px;padding:16px 18px}
.col{display:flex;flex-direction:column;gap:8px;min-width:0}
.brand{display:flex;align-items:center;gap:10px;height:120px}
.brand-mark{width:44px;height:44px;border-radius:50%;background:var(--red);flex:none}
.brand-name{font-family:'Oswald',sans-serif;font-weight:600;font-size:24px;line-height:1.05;color:var(--red);text-transform:uppercase}
.banner{background:var(--brown);color:var(--paper);font-family:'Oswald',sans-serif;font-weight:600;font-size:19px;
  text-align:center;padding:4px 0;clip-path:polygon(0 0,100% 0,96% 50%,100% 100%,0 100%,4% 50%)}
.note{font-size:11px;line-height:1.3;color:var(--brown-soft)}
.item{display:flex;justify-content:space-between;font-size:12.5px;font-weight:700;text-transform:uppercase;padding:1px 0;white-space:nowrap}
.item span:last-child{color:var(--red)}
.sub{font-size:10.5px;color:var(--brown-soft);padding-left:6px;line-height:1.3}
.soda-box{display:flex;gap:8px;align-items:stretch}
.soda-list{background:var(--yellow);padding:6px 10px;flex:1}
.soda-list .item span:last-child{color:var(--brown)}
.art{border-radius:4px}
.soda-art{width:80px;background:linear-gradient(#c9a77a,#a88458)}
.flavor-art{height:70px;background:linear-gradient(90deg,#d8c39c,#c7ab7d)}
.herb-art{height:60px;background:linear-gradient(90deg,#cfb88d,#bfa277)}
.flavors{display:grid;grid-template-columns:1.3fr 1fr;font-size:10.5px;font-weight:700;text-transform:uppercase;gap:3px 8px;padding:0 4px;white-space:nowrap}
.info{border:2px solid var(--brown);padding:8px 10px;font-size:11px;line-height:1.35}
.info strong{font-family:'Oswald',sans-serif;font-weight:600;font-size:12px;color:var(--brown)}
.hours{display:grid;grid-template-columns:auto 1fr;gap:1px 10px;margin-top:5px;font-weight:700;text-transform:uppercase}
.hours span:nth-child(odd){color:var(--red)}
.follow{font-size:11px;font-weight:700;color:var(--brown);text-align:center}
</style>
</head>
<body>
<main class="menu">
  <section class="col">
    <div class="brand">
      <div class="brand-mark"></div>
      <div class="brand-name">Morales's<br>Burrito Hut</div>
    </div>
    <div class="banner">Tacos</div>
    <div class="item"><span>Tacos</span><span>$4.75 ea</span></div>
    <p class="note">Selección de carne, cilantro, cebolla, salsa roja o verde<br>Choice of meat, cilantro, onion, red or green salsa</p>
    <p class="note"><b>Selección de carne / Choice of Meat</b></p>
    <div class="item"><span>Pollo / Chicken</span><span></span></div>
    <div class="item"><span>Carne Asada / Steak</span><span></span></div>
    <div class="item"><span>Al Pastor / Marinated Pork</span><span></span></div>
    <div class="item"><span>Chorizo / Sausage</span><span></span></div>
    <div class="item"><span>Carnitas / Pulled Pork</span><span></span></div>
    <div class="item"><span>Mixta / Steak &amp; Sausage</span><span>+$0.75</span></div>
    <div class="item"><span>Suadero / Brisket</span><span>+$0.75</span></div>
    <div class="item"><span>Lengua / Beef Tongue</span><span>+$0.75</span></div>
    <div class="item"><span>Tripa / Beef Tripe</span><span>+$0.75</span></div>
  </section>

  <section class="col">
    <div class="banner">Appetizers / Antojitos</div>
    <div class="item"><span>Tacos Dorados de Pollo</span><span>$15.00</span></div>
    <div class="item"><span>Tacos Dorados de Carne</span><span>$15.00</span></div>
    <div class="item"><span>Quesadilla</span><span>$10.00</span></div>
    <p class="sub">Pollo (Chicken) | Carne Asada (Steak) | Queso (Cheese)</p>
    <div class="item"><span>Pupusa Revueltas</span><span>$3.50</span></div>
    <p class="sub">Chicharrón y Queso</p>
    <div class="item"><span>Pupusa Queso</span><span>$3.50</span></div>
    <div class="banner">Especiales / Specials</div>
    <div class="item"><span>#1 4 Tacos</span><span>$14.00</span></div>
    <div class="item"><span>#2 4 Tacos Dorados / Flautas</span><span></span></div>
    <p class="sub">Pollo, Crema, Queso Fresco, Aguacate<br>Chicken, Cream, Queso Fresco, Avocado</p>
    <div class="item"><span>#3 Chicharrones 1lb ★</span><span>$25.00</span></div>
    <p class="sub">★ Cantidad limitada y temporada / Limited Quantity / Seasonal</p>
    <div class="soda-box">
      <div class="soda-list">
        <div class="item"><span>Fizzo</span><span>$2.00</span></div>
        <div class="item"><span>Zestle</span><span>$2.00</span></div>
        <div class="item"><span>Water</span><span>$1.50</span></div>
        <div class="item"><span>Frutinas</span><span>$3.00</span></div>
      </div>
      <div class="art soda-art" role="img" aria-label="Sketch of soda bottles"></div>
    </div>
  </section>

  <section class="col">
    <div class="banner">Bebidas / Beverages</div>
    <div class="item"><span>Horchata</span><span>$6.00</span></div>
    <div class="item"><span>Agua Fresca</span><span>$5.00</span></div>
    <div class="art flavor-art" role="img" aria-label="Sketch of fresh fruit"></div>
    <div class="banner">Sabor / Flavor</div>
    <div class="flavors">
      <span>Lemonade / Limonada</span><span>Pineapple / Piña</span>
      <span>Hibiscus / Jamaica</span><span>Melon</span>
      <span>Watermelon / Sandía</span><span>Mango</span>
    </div>
    <div class="info">
      <strong>812 W Orchard Ct, Entrada / Entrance Brightway Shopping Center, Maple Hollow, NY 11845</strong>
      <div class="hours">
        <span>Friday</span><span>6 PM – 11:30 PM</span>
        <span>Saturday</span><span>1 PM – 11:30 PM</span>
        <span>Sunday</span><span>1 PM – 11:00 PM</span>
      </div>
    </div>
    <p class="follow">Síganos / Follow Us: @moralesburritohut</p>
    <div class="art herb-art" role="img" aria-label="Sketch of peppers and herbs"></div>
  </section>
</main>
</body>
</html>
```